Professional Package for CPA Firm

We would like a stationery design for our new CPA Firm based in Atlanta, GA called 'Vale 8'. We work with investors to help grow investments, tax free. We would like the design to have a professional/minimal look with a 'wow' factor. We need 9.5″ x 4.125″, 9x12, and 10x13 mailing envelopes, business cards, and a letterhead. We have a logo that is already complete. For the letterhead, we would like to have space to put credentials at the bottom of the page

Industry/Entity Type

CPA, Accounting

```html
<!DOCTYPE html>
<html lang="en">
<head>
<meta charset="utf-8">
<title>Vale 8 – Business Card</title>
<link rel="stylesheet" href="https://fonts.googleapis.com/css2?family=Lato:wght@400;700&family=Montserrat:wght@500;700&family=Oswald:wght@600&display=swap">
<style>
  :root {
    --navy: #0d2b3e;
    --deep: #03202f;
    --teal: #1ba3b3;
    --red: #f4454d;
    --ink: #4f555a;
    --paper: #ffffff;
    --backdrop: #e9ebec;
  }
  * { box-sizing: border-box; margin: 0; padding: 0; }
  html, body { width: 1200px; height: 1200px; overflow: hidden; background: var(--backdrop); }
  .canvas { position: relative; width: 1200px; height: 1200px; }

  .card { position: absolute; left: 200px; width: 800px; height: 457px; overflow: hidden; }
  .card-front { top: 120px; background: var(--paper); }
  .card-back { top: 660px; }

  .brand { position: absolute; left: 60px; top: 140px; }
  .brand-name {
    font-family: "Montserrat", sans-serif; font-weight: 700; font-size: 56px;
    color: var(--navy); letter-spacing: 1px; line-height: 1;
  }
  .brand-tagline {
    font-family: "Montserrat", sans-serif; font-weight: 500; font-size: 15px;
    color: var(--navy); letter-spacing: 1px; margin-top: 8px;
  }

  .address {
    position: absolute; left: 52px; top: 268px;
    font-family: "Lato", sans-serif; font-size: 18px; line-height: 22px; color: var(--ink);
  }
  .contacts { position: absolute; left: 52px; top: 324px; list-style: none; }
  .contacts li {
    display: flex; align-items: center; gap: 10px; height: 23px;
    font-family: "Lato", sans-serif; font-size: 18px; color: var(--ink);
  }
  .contacts svg { width: 14px; height: 14px; fill: var(--teal); flex: none; }

  .person { position: absolute; right: 52px; top: 314px; text-align: right; }
  .person-name {
    font-family: "Oswald", sans-serif; font-weight: 600; font-size: 31px;
    color: var(--navy); line-height: 1; letter-spacing: 0.5px;
  }
  .person-role { font-family: "Lato", sans-serif; font-size: 18px; color: var(--teal); margin-top: 6px; }

  .card-stripe { position: absolute; left: 0; bottom: 0; width: 800px; height: 18px; }

  .back-field {
    position: absolute; inset: 0;
    background: linear-gradient(100deg, #0b5478 0%, #063651 45%, #021a28 100%);
  }
  .back-brand {
    position: absolute; left: 598px; top: 346px;
    font-family: "Montserrat", sans-serif; font-weight: 700; font-size: 34px;
    color: var(--paper); letter-spacing: 1px;
  }
</style>
</head>
<body>
<div class="canvas">

  <section class="card card-front">
    <div class="brand">
      <div class="brand-name">VALE 8</div>
      <div class="brand-tagline">CPAs and Tax Advisors</div>
    </div>

    <p class="address">4120 Linden Court<br>Atlanta, Georgia 30305</p>

    <ul class="contacts">
      <li><svg viewBox="0 0 16 16"><path d="M3.5 1l3 3-1.6 2a9 9 0 0 0 5.1 5.1l2-1.6 3 3-2 2C7 15 1 9 1.5 3z"/></svg>404-555-0182</li>
      <li><svg viewBox="0 0 16 16"><path d="M4 0h8v16H4zM5.5 1.5v11h5v-11z"/></svg>404-555-0247</li>
      <li><svg viewBox="0 0 16 16"><path d="M1 4h14v9H1zM2 5l6 4 6-4v-.5H2z"/></svg>info@vale8.com</li>
      <li><svg viewBox="0 0 16 16"><circle cx="8" cy="8" r="7"/></svg>www.vale8.com</li>
    </ul>

    <div class="person">
      <div class="person-name">DANIEL REYES</div>
      <div class="person-role">President</div>
    </div>

    <svg class="card-stripe" viewBox="0 0 800 18" preserveAspectRatio="none">
      <polygon points="0,0 476,0 471,18 0,18" fill="var(--navy)"/>
      <polygon points="481,0 628,0 623,18 476,18" fill="var(--teal)"/>
      <polygon points="633,0 800,0 800,18 628,18" fill="var(--red)"/>
    </svg>
  </section>

  <section class="card card-back">
    <div class="back-field" role="img" aria-label="Repeating pattern of the brand mark on a deep navy gradient"></div>
    <div class="back-brand">VALE 8</div>
  </section>

</div>
</body>
</html>
```